Skin cancer clinic services trifold brochure

Need trifold brochure listing skin cancer services our clinic provides, staff information, location and brief about skin cancer with colours similar to our web site www.Tolvarin.clinic. I will provide more information regarding services and staff but want this colourful and standout as it will be given to other referring doctors or patients

Target Market(s)

Age 40 to 80 years

Industry/Entity Type

Medical

Font styles to use
Serif

Colors

Designer to choose colors to be used in the design.

Requirements
Must have
• Logo, services, contact info, beach or sun look and colours similar to web site or logo

```html
<!DOCTYPE html>
<html lang="en">
<head>
<meta charset="utf-8">
<title>Tolvarin Skin Cancer Clinic – Trifold Brochure</title>
<link rel="stylesheet" href="https://fonts.googleapis.com/css2?family=Marcellus&family=Source+Sans+3:ital,wght@0,400;0,600;0,700;1,400;1,600;1,700&family=Courgette&family=Noticia+Text:ital@1&display=swap">
<style>
:root{
  --bg:#e6e6e6;
  --sun:#f2b21b;
  --sun-light:#f9d36e;
  --flame:#ee7d1f;
  --ember:#e5661f;
  --leaf:#2f7d2e;
  --leaf-light:#5aa03a;
  --sky:#2f9ad6;
  --sky-deep:#1f7fc0;
  --ink:#3a2a12;
  --text:#444;
  --cream:#fffdf7;
  --cream-2:#fdf6e2;
  --white:#fff;
}
*{box-sizing:border-box;margin:0;padding:0}
html,body{width:683px;height:1200px;overflow:hidden}
body{background:var(--bg);position:relative;font-family:"Source Sans 3",Arial,sans-serif;color:var(--text)}

.spread{position:absolute;left:0;width:683px;height:500px;display:grid;grid-template-columns:repeat(3,1fr);box-shadow:0 4px 14px rgba(0,0,0,.25)}
.spread--outside{top:60px}
.spread--inside{top:640px}
.panel{position:relative;overflow:hidden;height:500px}

/* ---------- Specialised treatments panel ---------- */
.treatments{background:var(--sun);color:var(--ink);padding:58px 14px 0 14px}
.treatments__ribbon{position:absolute;top:24px;left:8px;right:8px;height:24px;background:var(--ember);color:var(--white);font-style:italic;font-weight:700;font-size:14px;line-height:24px;padding-left:12px;transform:skewY(-2deg)}
.treatments h3{font-size:8.5px;font-weight:700;margin-top:9px}
.treatments p{font-size:7px;line-height:1.35;font-style:italic}

/* ---------- Booking panel ---------- */
.booking{background:var(--sky);color:var(--white);text-align:center;padding-top:22px}
.booking__label{font-size:12px;letter-spacing:.6px;font-weight:400}
.booking__phone{font-size:25px;font-weight:700;font-style:italic;margin-top:6px;letter-spacing:.5px}
.booking__email{font-size:11.5px;letter-spacing:.6px;margin-top:2px}
.booking__card{margin:12px auto 0;width:180px;height:250px;background:var(--white);padding:12px 10px}
.booking__brand{display:flex;align-items:center;justify-content:space-between}
.wordmark{display:flex;align-items:center;gap:5px;font-family:"Source Sans 3",sans-serif;font-weight:700;color:var(--flame);letter-spacing:1.2px}
.wordmark__dot{width:10px;height:10px;border-radius:50%;background:var(--flame)}
.booking__brand .wordmark{font-size:15px}
.badge{width:36px;height:36px;background:var(--sky-deep);border-radius:4px}
.booking__map{margin-top:12px;height:170px;background:linear-gradient(135deg,#eef0ec,#dfe6df 55%,#f3e7c4);border:1px solid #ddd}
.booking__url{display:inline-block;margin-top:18px;background:var(--flame);border-radius:12px;padding:3px 16px;font-weight:700;font-size:12px;letter-spacing:1.4px}
.booking__address{font-size:9.5px;line-height:1.4;margin-top:10px;font-weight:600}

/* ---------- Cover panel ---------- */
.cover svg.cover__art{position:absolute;inset:0}
.cover__title{position:absolute;top:34px;left:0;right:0;text-align:center;font-family:"Marcellus",serif;color:var(--sun);font-size:28px;letter-spacing:1px}
.cover__question{position:absolute;top:72px;left:0;right:0;text-align:center;font-family:"Marcellus",serif;color:var(--white);font-size:15px;line-height:1.15;letter-spacing:.5px}
.cover__tagline{position:absolute;top:114px;left:0;right:0;text-align:center;font-family:"Courgette",cursive;color:var(--flame);font-size:12.5px}
.cover__logo{position:absolute;left:50px;top:348px;width:116px;height:116px;border-radius:50%;background:var(--white);display:flex;align-items:center;justify-content:center}
.cover__logo .wordmark{font-size:17px}
.cover__url{position:absolute;bottom:16px;left:0;right:0;text-align:center;color:var(--white);font-weight:700;font-size:12.5px;letter-spacing:1.6px}

/* ---------- Inside panels ---------- */
.inside{background:var(--cream);padding:18px 14px 0}
.inside--mid{background:var(--cream-2)}
.inside h2{font-family:"Source Sans 3",sans-serif;color:var(--flame);font-size:15px;font-weight:700;margin-bottom:4px}
.inside p{font-size:7.2px;line-height:1.4;color:var(--text)}
.inside strong{color:var(--ink)}
.prompt{font-family:"Noticia Text",serif;font-style:italic;color:var(--sky-deep);font-size:10px;margin:7px 0 10px}
.lead{color:var(--sky-deep);font-weight:700;font-size:9.5px;margin-top:8px}
.welcome{color:var(--flame);font-style:italic;font-weight:600;font-size:8px;line-height:1.3}
.staff{list-style:none;margin:6px 0 10px}
.staff li{position:relative;padding-left:12px;font-size:7px;line-height:1.3;margin-bottom:3px}
.staff li::before{content:"";position:absolute;left:0;top:2px;width:7px;height:7px;border-radius:50%;background:var(--sun)}
.services p{margin-bottom:5px}
.callout{background:var(--sky);color:var(--white);border-radius:8px;padding:7px 9px;font-size:7.4px;line-height:1.35;font-style:italic;font-weight:600;margin-bottom:9px}
.inside--right p{margin-bottom:5px}
.pain-band{position:absolute;left:0;right:0;top:360px;height:58px;background:var(--sun-light)}
.pain-text{position:absolute;left:14px;right:14px;top:364px}
.band{position:absolute;left:0;right:0}
.photo-slot{position:absolute;left:0;right:0;bottom:0}
.photo-round{position:absolute;width:78px;height:78px;border-radius:50%;border:3px solid var(--white)}
</style>
</head>
<body>

<!-- Outside spread -->
<section class="spread spread--outside">
  <article class="panel treatments">
    <div class="treatments__ribbon">Specialised Treatments</div>
    <h3>Surgical Procedures</h3>
    <p>Our doctors are proficient in surgical procedures from simple diagnostic biopsies or elliptical excisions to advanced procedures including skin grafts and surgical flap repair, all under a local anaesthetic.</p>
    <h3>Radiotome Radiofrequency procedures</h3>
    <p>Surgical options include high frequency radiosurgical devices for scalpel-free surgery. It allows our doctors to use radiowaves instead of scalpels for selected skin cancer procedures and cosmetic procedures, including removal of spider veins, skin tags and benign lesions, with minimal thermal damage, bleeding and recovery time.</p>
    <h3>Margin Controlled Surgery</h3>
    <p>Also known as Slow Mohs or Delayed Closure – a process where aggressive skin cancers are not closed after excision until the histological clearance is known. This can minimise the need for larger excisions and benefits cosmetically sensitive regions such as the nose, ears and face.</p>
    <h3>Non-surgical treatments and preventative therapy options</h3>
    <p>Our goal is to prevent and treat skin cancer in the least invasive way possible, as appropriate. This includes preventative care including Vitamin B3 benefits, sun safe practices, topical therapies and liquid nitrogen for solar keratoses or superficial non-melanoma skin cancers.</p>
    <h3>Cosmetic Services</h3>
    <p>Tolvarin approaches our skin cancer patient holistically and by appointment we can offer advice and treatment regarding skin pigmentation, troublesome bumps and lumps and more. Please see our web site at www.Tolvarin.clinic for more information.</p>
  </article>

  <article class="panel booking">
    <div class="booking__label">BOOK AN APPOINTMENT</div>
    <div class="booking__phone">1300 55 8190</div>
    <div class="booking__email">admin@Tolvarin.clinic</div>
    <div class="booking__card">
      <div class="booking__brand">
        <div class="wordmark"><span class="wordmark__dot"></span>TOLVARIN</div>
        <div class="badge" role="img" aria-label="Accreditation badge"></div>
      </div>
      <div class="booking__map" role="img" aria-label="Street map showing the clinic location"></div>
    </div>
    <div class="booking__url">www.Tolvarin.clinic</div>
    <div class="booking__address">Suite 3, 118 Harbour Road<br>Kelsey, NSW 2260<br>Fax: 4311 0628</div>
  </article>

  <article class="panel cover">
    <svg class="cover__art" width="228" height="500" viewBox="0 0 228 500" aria-hidden="true">
      <defs>
        <linearGradient id="leafGrad" x1="0" y1="0" x2="0" y2="1">
          <stop offset="0" stop-color="#2b7a2c"/>
          <stop offset="1" stop-color="#5aa03a"/>
        </linearGradient>
      </defs>
      <rect width="228" height="500" fill="#f2b21b"/>
      <rect width="228" height="340" fill="url(#leafGrad)"/>
      <path d="M0 372 C80 362 170 322 228 252 V500 H0 Z" fill="#f9d36e"/>
      <path d="M0 384 C90 374 175 334 228 268 V500 H0 Z" fill="#ee7d1f"/>
      <path d="M0 398 C95 388 180 350 228 288 V500 H0 Z" fill="#f2b21b"/>
    </svg>
    <svg width="228" height="500" viewBox="0 0 228 500" style="position:absolute;inset:0" role="img" aria-label="Photo of a smiling senior couple outdoors">
      <defs>
        <linearGradient id="photoGrad" x1="0" y1="0" x2="1" y2="1">
          <stop offset="0" stop-color="#8fb65a"/>
          <stop offset=".5" stop-color="#d9b89a"/>
          <stop offset="1" stop-color="#6f7f8c"/>
        </linearGradient>
      </defs>
      <path d="M30 150 H228 V252 C170 322 80 362 30 366 Z" fill="url(#photoGrad)" opacity=".85"/>
    </svg>
    <div class="cover__title">SKIN CANCER</div>
    <div class="cover__question">WHEN WAS YOUR<br>LAST SKIN CHECK?</div>
    <div class="cover__tagline">"Comfort In Your Skin"</div>
    <div class="cover__logo"><div class="wordmark"><span class="wordmark__dot"></span>TOLVARIN</div></div>
    <div class="cover__url">www.Tolvarin.clinic</div>
  </article>
</section>

<!-- Inside spread -->
<section class="spread spread--inside">
  <article class="panel inside inside--left">
    <h2>Did you know?</h2>
    <p>Skin cancers account for 80% of all newly diagnosed cancers with two in three Australians diagnosed with skin cancer by the time they are 70. Although over 90% of skin cancers are due to over exposure to UV light, some are caused by chemical exposure or are hereditary. Over 2000 Australians die from skin cancer each year.</p>
    <div class="prompt">Have you had your skin checked lately?</div>
    <h2>About Us</h2>
    <p>Tolvarin Skin Cancer Clinic is a purpose-built skin cancer clinic dedicated to providing the highest-level patient care to the Central Coast community and surrounding regions. Our skilled doctors and nurses have extensive experience and advanced training in Skin Cancer Medicine in order to provide quality care to our patients. We specialise in a comprehensive approach to skin with preventive skin cancer care, expert diagnostic dermoscopy skills highlighting artificial intelligent analytics, and definitive surgical and medical treatments of skin cancers.</p>
    <div class="lead">Skin cancer medicine is all we do.</div>
    <div class="welcome">We welcome you to "virtually" walk through our clinic at www.Tolvarin.clinic</div>
    <svg class="band" style="bottom:84px" width="228" height="30" viewBox="0 0 228 30" aria-hidden="true">
      <path d="M0 14 C80 4 160 24 228 10 V30 H0 Z" fill="#ee7d1f"/>
      <path d="M0 22 C80 12 160 30 228 18 V30 H0 Z" fill="#f2b21b"/>
    </svg>
    <div class="photo-slot" style="height:86px;background:linear-gradient(160deg,#7fb3c9,#e8d2a6 45%,#d9b37c)" role="img" aria-label="Photo of a starfish on a sandy beach"></div>
    <div class="photo-round" style="left:122px;bottom:46px;background:linear-gradient(135deg,#e7c7b0,#b9927a)" role="img" aria-label="Photo of a skin check with a dermatoscope"></div>
  </article>

  <article class="panel inside inside--mid">
    <h2>Our Staff</h2>
    <p><strong>At Tolvarin Skin Cancer Clinic, our highly qualified administrative staff, nurses and doctors are an integral part of the team ensuring excellent clinical care is provided to our patients. We currently have 5 experienced local doctors:</strong></p>
    <ul class="staff">
      <li><strong>Dr. Mara Quinlan:</strong> BMed, FRACGP, Diploma Skin Cancer Medicine/Surgery, Diploma Aesthetic Medicine</li>
      <li><strong>Dr. Tessa Hollis:</strong> BMed, FRACGP, Diploma Skin Cancer Medicine/Surgery</li>
      <li><strong>Dr. Nadia Corwell:</strong> MBBS, FRACGP</li>
      <li><strong>Dr. Owen Pritchard:</strong> MBBS (Syd), Dip Law</li>
      <li><strong>Dr. Elise Marwood:</strong> MBBS (Hons), FRACGP, Cert Skin Cancer Medicine</li>
    </ul>
    <h2>Professional Skin Services</h2>
    <div class="services">
      <p><strong>Advanced Skin Cancer Detection</strong> with detailed Full Body skin checks using dermoscopy and technology to minimise unnecessary excisions.</p>
      <p><strong>Individual Mole mapping and full body photography</strong> utilising intelligent skin analytics with ScanLedger – an artificial intelligence-powered platform which provides tools for documenting and diagnosing skin cancers and evidence-based care. Powered by AI algorithms, it will identify changes to the skin over time and support early clinical decisions and diagnosis.</p>
      <p><strong>SpotTrace Skin Imaging System</strong> which captures high-quality images using DermaVue – clinically proven technology which provides a unique level of detail and information from up to 2mm beneath the skin's surface allowing deeper assessment and risk of melanoma.</p>
    </div>
    <svg class="band" style="bottom:70px" width="228" height="26" viewBox="0 0 228 26" aria-hidden="true">
      <path d="M0 10 C80 22 160 2 228 12 V26 H0 Z" fill="#f2b21b"/>
    </svg>
    <div class="photo-slot" style="height:72px;background:linear-gradient(160deg,#9cc8de,#cfe3ea 50%,#e9dcc0)" role="img" aria-label="Photo of a family enjoying the beach"></div>
    <div class="photo-round" style="left:18px;bottom:22px;background:linear-gradient(135deg,#f0d9c6,#c8a48a)" role="img" aria-label="Photo of a doctor examining a patient's skin"></div>
  </article>

  <article class="panel inside inside--right">
    <div class="callout">Early detection of skin cancers is vital for the best outcome. Tolvarin has invested in technology and research to provide the latest diagnostic services and treatments to meet the needs of our patients.</div>
    <p><strong>Purpose Built Skin Cancer Facility</strong> providing Surgical treatments in 2 dedicated fully equipped theatres and treatment room staffed by skilled skin cancer medicine nurses.</p>
    <p><strong>Large referral basis</strong> for our patients that may require extensive therapy for their skin cancers, including Radiotherapy for cosmetically sensitive areas that are not optimally treated with surgery. Advanced care under the Brennock Melanoma Centre or Mohs Surgery and more.</p>
    <p><strong>Priority Spot Checks</strong> – appointments are set aside every day for urgent suspicious lesions allowing for quick evaluation, whether for an existing or new patient. Although we welcome GP referrals, it is not required.</p>
    <p><strong>GP Team Approach</strong> – Tolvarin believes it is important that an integrated team approach to a patient's skin cancer care is important, and communication of histological results and findings are shared with their GP upon permission.</p>
    <div class="pain-band" aria-hidden="true"></div>
    <p class="pain-text"><strong>Pain minimisation Techniques</strong> – Topical numbing creams and ChillPoint numbing agents are available to minimise tenderness that can come with local anaesthetics. Our theatres are equipped with overhead projectors playing calming nature scenes to ensure our patients are comfortable.</p>
    <svg class="band" style="bottom:72px" width="228" height="14" viewBox="0 0 228 14" aria-hidden="true">
      <path d="M0 4 C80 14 160 0 228 6 V14 H0 Z" fill="#ee7d1f"/>
    </svg>
    <div class="photo-slot" style="height:76px;background:linear-gradient(160deg,#e9dcc4,#c9a27a 55%,#8e6a4a)" role="img" aria-label="Photo of a woman in a sun hat relaxing on the beach"></div>
  </article>
</section>

</body>
</html>
```